Product packaging design for lentils

Looking to create a design for lentils in 4lb format. We are looking to create a base design for the bags, and then from there will have additional designs for the different products with different product name, barcodes and nutritional information.

Industry/Entity Type

Food

```html
<!DOCTYPE html>
<html lang="en">
<head>
<meta charset="UTF-8">
<title>Harvestwell Red Split Lentils – 4lb Bag</title>
<link href="https://fonts.googleapis.com/css2?family=Open+Sans:wght@400;600;700;800&family=Playball&family=Oswald:wght@500;700&display=swap" rel="stylesheet">
<style>
  :root{
    --backdrop:#efeae3;
    --bag-red:#e0281b;
    --bag-red-dark:#b91a10;
    --lentil-light:#f7a04a;
    --lentil-mid:#ee7a2a;
    --lentil-deep:#d9581c;
    --gold:#d9b25a;
    --gold-light:#f1d592;
    --green:#1f8a3a;
    --badge-black:#161616;
    --badge-yellow:#f6d21c;
    --seal-navy:#173f78;
    --white:#ffffff;
  }
  *{margin:0;padding:0;box-sizing:border-box}
  html,body{width:1186px;height:1200px;overflow:hidden;background:var(--backdrop)}
  .canvas{position:relative;width:1186px;height:1200px}
  .bag{position:absolute;left:0;top:0}
  .text-sans{font-family:"Open Sans",sans-serif}
  .reseal-note{font-family:"Open Sans",sans-serif;font-size:19px;fill:var(--white);fill-opacity:.55}
  .brand-name{font-family:"Open Sans",sans-serif;font-weight:800;font-size:54px;fill:var(--white)}
  .product-script{font-family:"Playball",cursive;font-size:62px;fill:var(--white)}
  .product-name{font-family:"Open Sans",sans-serif;font-weight:800;font-size:72px;fill:var(--white);letter-spacing:1px}
  .product-sub{font-family:"Open Sans",sans-serif;font-weight:600;font-size:40px;fill:var(--white)}
  .net-weight{font-family:"Open Sans",sans-serif;font-weight:800;font-size:24px;fill:var(--white)}
  .stat-label{font-family:"Oswald",sans-serif;font-weight:500;font-size:20px;fill:var(--white)}
  .stat-small{font-family:"Open Sans",sans-serif;font-size:12px;fill:var(--white)}
  .stat-value{font-family:"Oswald",sans-serif;font-weight:700;font-size:32px;fill:var(--badge-black)}
  .claim-big{font-family:"Open Sans",sans-serif;font-weight:800;font-size:15px;fill:var(--white)}
  .claim-small{font-family:"Open Sans",sans-serif;font-weight:700;font-size:10px;fill:var(--white)}
</style>
</head>
<body>
<div class="canvas">
<svg class="bag" width="1186" height="1200" viewBox="0 0 1186 1200" xmlns="http://www.w3.org/2000/svg">
  <defs>
    <radialGradient id="lentil-fill" cx="50%" cy="50%" r="70%">
      <stop offset="0" stop-color="var(--lentil-light)"/>
      <stop offset=".6" stop-color="var(--lentil-mid)"/>
      <stop offset="1" stop-color="var(--lentil-deep)"/>
    </radialGradient>
    <clipPath id="bag-clip"><rect x="60" y="30" width="1066" height="1140" rx="6"/></clipPath>
  </defs>

  <!-- bag body -->
  <g clip-path="url(#bag-clip)">
    <rect class="bag-body" x="60" y="30" width="1066" height="1140" fill="var(--bag-red)"/>
    <!-- seal strips -->
    <rect class="top-seal" x="60" y="30" width="1066" height="44" fill="var(--bag-red-dark)" opacity=".35"/>
    <rect class="bottom-seal" x="60" y="1126" width="1066" height="44" fill="var(--bag-red-dark)" opacity=".35"/>

    <!-- resealable line -->
    <line x1="90" y1="128" x2="300" y2="128" stroke="var(--gold)" stroke-width="3" stroke-dasharray="6 4"/>
    <line x1="886" y1="128" x2="1096" y2="128" stroke="var(--gold)" stroke-width="3" stroke-dasharray="6 4"/>
    <text class="reseal-note" x="593" y="135" text-anchor="middle">Resealable for Freshness | Refermable pour Fraîcheur</text>

    <!-- product window -->
    <path class="product-window" role="img" aria-label="Photograph of red split lentils filling the bag window"
          d="M60,210 L380,292 Q593,392 806,292 L1126,210 L1126,1000 L60,1000 Z" fill="url(#lentil-fill)"/>
    <path d="M60,210 L380,292 Q593,392 806,292 L1126,210" fill="none" stroke="var(--gold)" stroke-width="5"/>
    <line x1="60" y1="1000" x2="1126" y2="1000" stroke="var(--gold)" stroke-width="5"/>
  </g>

  <!-- brand -->
  <g class="brand">
    <circle cx="418" cy="266" r="16" fill="var(--green)"/>
    <text class="brand-name" x="448" y="285">Harvestwell</text>
  </g>

  <!-- quality seal -->
  <g class="quality-seal">
    <circle cx="593" cy="462" r="62" fill="var(--gold)"/>
    <circle cx="593" cy="462" r="54" fill="var(--seal-navy)"/>
  </g>

  <!-- product label -->
  <g class="product-label">
    <path d="M265,520 Q593,490 921,520 L921,820 Q593,850 265,820 Z" fill="var(--bag-red)" stroke="var(--gold)" stroke-width="5"/>
    <path d="M280,534 Q593,506 906,534 L906,806 Q593,834 280,806 Z" fill="none" stroke="var(--gold-light)" stroke-width="1.5" opacity=".7"/>
    <text class="product-script" x="593" y="590" text-anchor="middle">Red Split Lentils</text>
    <line x1="330" y1="616" x2="856" y2="616" stroke="var(--bag-red-dark)" stroke-width="2"/>
    <rect x="585" y="608" width="16" height="16" transform="rotate(45 593 616)" fill="var(--bag-red-dark)"/>
    <text class="product-name" x="593" y="693" text-anchor="middle">MASOOR DAL</text>
    <line x1="330" y1="716" x2="856" y2="716" stroke="var(--bag-red-dark)" stroke-width="2"/>
    <rect x="585" y="708" width="16" height="16" transform="rotate(45 593 716)" fill="var(--bag-red-dark)"/>
    <text class="product-sub" x="593" y="767" text-anchor="middle">SPLIT MASUR ROUGE</text>
    <rect x="588" y="779" width="8" height="8" transform="rotate(45 592 783)" fill="var(--bag-red-dark)"/>
    <text class="net-weight" x="593" y="812" text-anchor="middle">NET WT  4LB 1.81KG</text>
  </g>

  <!-- stats & claims row -->
  <g class="claims-row">
    <!-- fiber -->
    <g class="stat-badge">
      <rect x="286" y="946" width="94" height="112" rx="10" fill="var(--gold)"/>
      <rect x="291" y="951" width="84" height="60" rx="7" fill="var(--badge-black)"/>
      <rect x="291" y="1011" width="84" height="42" rx="7" fill="var(--badge-yellow)"/>
      <text class="stat-label" x="333" y="978" text-anchor="middle">Fiber</text>
      <text class="stat-small" x="333" y="998" text-anchor="middle">Per Serving</text>
      <text class="stat-value" x="333" y="1045" text-anchor="middle">05g</text>
    </g>
    <!-- vegan -->
    <g class="claim-badge">
      <circle cx="449" cy="1002" r="54" fill="var(--gold)"/>
      <circle cx="449" cy="1002" r="49" fill="var(--green)"/>
      <path d="M449,996 C430,986 428,970 432,960 C446,966 452,980 449,996 Z M449,996 C468,986 470,970 466,960 C452,966 446,980 449,996 Z" fill="var(--white)"/>
      <text class="claim-big" x="449" y="1020" text-anchor="middle">100%</text>
      <text class="claim-small" x="449" y="1033" text-anchor="middle">VEGAN</text>
    </g>
    <!-- natural -->
    <g class="claim-badge">
      <circle cx="578" cy="1002" r="54" fill="var(--gold)"/>
      <circle cx="578" cy="1002" r="49" fill="var(--green)"/>
      <circle cx="578" cy="978" r="16" fill="none" stroke="var(--white)" stroke-width="3"/>
      <path d="M578,990 C570,982 572,972 582,966 C586,976 584,984 578,990 Z" fill="var(--white)"/>
      <text class="claim-big" x="578" y="1020" text-anchor="middle">100%</text>
      <text class="claim-small" x="578" y="1033" text-anchor="middle">NATURAL</text>
    </g>
    <!-- no additives -->
    <g class="claim-badge">
      <circle cx="707" cy="1002" r="54" fill="var(--gold)"/>
      <circle cx="707" cy="1002" r="49" fill="var(--green)"/>
      <circle cx="707" cy="978" r="15" fill="none" stroke="var(--white)" stroke-width="3"/>
      <line x1="696" y1="967" x2="718" y2="989" stroke="var(--white)" stroke-width="3"/>
      <text class="claim-big" x="707" y="1020" text-anchor="middle">NO</text>
      <text class="claim-small" x="707" y="1033" text-anchor="middle">ADDITIVES</text>
    </g>
    <!-- protein -->
    <g class="stat-badge">
      <rect x="781" y="946" width="94" height="112" rx="10" fill="var(--gold)"/>
      <rect x="786" y="951" width="84" height="60" rx="7" fill="var(--badge-black)"/>
      <rect x="786" y="1011" width="84" height="42" rx="7" fill="var(--badge-yellow)"/>
      <text class="stat-label" x="828" y="978" text-anchor="middle">Protein</text>
      <text class="stat-small" x="828" y="998" text-anchor="middle">Per Serving</text>
      <text class="stat-value" x="828" y="1045" text-anchor="middle">10g</text>
    </g>
  </g>
</svg>
</div>
</body>
</html>
```